Business Card Design for Marketing Firm

Looking for business card design for higher end marketing firm. Clean but impressionable/trendy. We are a marketing firm that represents manufacturers in the foodservice equipment and supply industry. Our customers are end users such has hotels, restaurants, country clubs, convention centers and casinos as well as distributors of restaurants supplies and equipment, and manufacturers of foodservice equipment and supplies.
Target Market(s)
Hotels, Restaurants, Supply & Equipment Distributors, Foodservice Manufacturers
Industry/Entity Type
Foodservice/Hospitality
Contact Information for Business Card
Name, Title, Contact Number, Email, Website, Social Media, Address
Requirements
Must have
- Clean & Simple but Serious and Impressionable

```html
<!DOCTYPE html>
<html lang="en">
<head>
<meta charset="utf-8">
<title>Meridian Hospitality Reps – Business Card</title>
<link rel="stylesheet" href="https://fonts.googleapis.com/css2?family=Libre+Baskerville:wght@400;700&family=Arimo:wght@400&display=swap">
<style>
  :root {
    --navy: #08087a;
    --navy-deep: #060664;
    --navy-soft: #3d3db8;
    --paper: #f4f4f6;
    --ink: #1c1c1c;
    --muted: #555;
    --grey-band: #5e5e5e;
    --backdrop: #2b2c2e;
  }
  * { box-sizing: border-box; margin: 0; padding: 0; }
  html, body { width: 1200px; height: 912px; overflow: hidden; }
  body {
    background: var(--backdrop);
    display: flex;
    align-items: center;
    justify-content: center;
    gap: 40px;
  }
  .card {
    width: 540px;
    height: 310px;
    border-radius: 18px;
    position: relative;
    overflow: hidden;
  }

  /* Front */
  .card-front {
    background: var(--navy-deep);
    display: flex;
    align-items: center;
    justify-content: center;
  }
  .front-wordmark {
    font-family: "Libre Baskerville", serif;
    font-weight: 400;
    font-size: 34px;
    letter-spacing: 4px;
    color: var(--navy-soft);
  }

  /* Back */
  .card-back { background: var(--paper); font-family: "Arimo", sans-serif; }

  .brand {
    position: absolute;
    right: 34px;
    top: 48px;
    text-align: right;
    font-family: "Libre Baskerville", serif;
    font-weight: 400;
    color: var(--navy);
  }
  .brand-name { font-size: 17px; letter-spacing: 1px; line-height: 1.2; }
  .brand-sub { font-size: 10px; letter-spacing: 2px; line-height: 1.2; }
  .brand-rule {
    margin-top: 6px;
    height: 1px;
    width: 230px;
    margin-left: auto;
    background: var(--navy);
  }

  .social {
    position: absolute;
    left: 30px;
    top: 30px;
    display: flex;
    gap: 5px;
  }
  .social span {
    width: 18px; height: 18px; border-radius: 50%;
    background: var(--navy);
  }

  .divider {
    position: absolute;
    left: 200px;
    right: 34px;
    top: 150px;
    height: 1px;
    background: var(--ink);
  }

  .address {
    position: absolute;
    right: 34px;
    top: 162px;
    text-align: right;
    font-size: 12.5px;
    line-height: 1.4;
    color: var(--ink);
  }

  .person { position: absolute; left: 30px; top: 160px; }
  .person-name {
    font-family: "Libre Baskerville", serif;
    font-weight: 700;
    font-size: 22px;
    letter-spacing: 0.5px;
    color: var(--navy);
  }
  .person-title { font-size: 13px; color: var(--muted); margin-top: 2px; }
  .person-rule { width: 140px; height: 1px; background: var(--ink); margin: 8px 0 8px; }

  .contact { list-style: none; }
  .contact li {
    display: flex;
    align-items: center;
    gap: 8px;
    font-size: 13px;
    line-height: 1.45;
    color: var(--ink);
  }
  .contact svg { width: 12px; height: 12px; fill: var(--navy); flex: none; }

  .band {
    position: absolute;
    left: 0; right: 0; bottom: 0;
    height: 14px;
    display: flex;
  }
  .band-navy { flex: 3; background: var(--navy); }
  .band-grey { flex: 1; background: var(--grey-band); }
</style>
</head>
<body>
  <section class="card card-front">
    <div class="front-wordmark">MERIDIAN</div>
  </section>

  <section class="card card-back">
    <div class="social" role="img" aria-label="Social media links">
      <span></span><span></span><span></span>
    </div>

    <div class="brand">
      <div class="brand-name">MERIDIAN HOSPITALITY</div>
      <div class="brand-sub">REPS</div>
      <div class="brand-rule"></div>
    </div>

    <div class="divider"></div>

    <address class="address" style="font-style:normal">
      2190 Harbor View Lane<br>
      Lakeside, NY 10990
    </address>

    <div class="person">
      <div class="person-name">EVAN CARTER</div>
      <div class="person-title">President</div>
      <div class="person-rule"></div>
      <ul class="contact">
        <li>
          <svg viewBox="0 0 24 24" aria-hidden="true"><path d="M6.6 10.8a15.1 15.1 0 0 0 6.6 6.6l2.2-2.2a1 1 0 0 1 1-.25 11.4 11.4 0 0 0 3.6.57 1 1 0 0 1 1 1V20a1 1 0 0 1-1 1A17 17 0 0 1 3 4a1 1 0 0 1 1-1h3.5a1 1 0 0 1 1 1c0 1.25.2 2.45.57 3.57a1 1 0 0 1-.25 1z"/></svg>
          (555) 0142-7788
        </li>
        <li>
          <svg viewBox="0 0 24 24" aria-hidden="true"><path d="M2 5h20v14H2z M4 7v.4l8 5 8-5V7l-8 5z" fill-rule="evenodd"/></svg>
          name@MERIDIAN.com
        </li>
        <li>
          <svg viewBox="0 0 24 24" aria-hidden="true"><circle cx="12" cy="12" r="10"/></svg>
          www.MERIDIAN.com
        </li>
      </ul>
    </div>

    <div class="band"><div class="band-navy"></div><div class="band-grey"></div></div>
  </section>
</body>
</html>
```